KRL Stationery Design Project

Dear Designers,
We need a new stationery design for company to match our new logo.
Designers should provide a design for the following:
1. Business Card: 3.5x2 Inches.
2. Letterhead: A4 size.
3. Envelops: 25x35.5 Cm.
You can keep the Arabic name at the bottom of the logo Or you can use the separate attached Arabic Name.
Please refer to the attached logo guide for design information.
Sample Business Card information:
Name: Tarek Sowan
Position: Operation Manager
Tel: +966 920007164 Ex. 500
Fax: +966 (3)8842617
Mob: +966 (5)00263817
email: tarek@krl-example.com.sa
URL: www.krl-example.com.sa
Address:
Nakheel Heights, Suite 718
Zayed bin Omar Str.
Khobar, 31847
Saudi Arabia
Updates
Dear All,
Please note, we had uploaded our logo along with Arabic writing in Adobe illustrator format (.ai).
Regards,
Karim
Dear All,
A sample data for the business card had been added as per your request.
Regards,
Karim

```html
<!DOCTYPE html>
<html lang="en">
<head>
<meta charset="utf-8">
<title>KRL Business Card</title>
<link rel="stylesheet" href="https://fonts.googleapis.com/css2?family=Open+Sans:ital,wght@0,400;0,700;1,700&display=swap">
<style>
  :root {
    --backdrop: #2a2a2a;
    --card: #ffffff;
    --navy: #12305a;
    --grey: #939598;
    --ink: #333333;
  }
  * { margin: 0; padding: 0; box-sizing: border-box; }
  html, body { width: 960px; height: 1200px; overflow: hidden; }
  body {
    position: relative;
    background: var(--backdrop);
    font-family: "Open Sans", Arial, sans-serif;
    color: var(--ink);
  }
  .card {
    position: absolute;
    width: 840px;
    background: var(--card);
    border-radius: 30px;
    overflow: hidden;
  }
  .card--front { left: 60px; top: 55px; height: 483px; }
  .card--back { left: 57px; top: 624px; height: 480px; }

  .brand {
    position: absolute;
    display: flex;
    align-items: center;
    color: var(--navy);
    font-weight: 700;
    line-height: 1;
  }
  .brand__mark { background: var(--navy); }
  .card--front .brand { left: 48px; top: 80px; gap: 22px; font-size: 96px; }
  .card--front .brand__mark { width: 40px; height: 40px; }
  .card--back .brand {
    left: 0; right: 0; top: 150px;
    justify-content: center; gap: 34px; font-size: 150px;
  }
  .card--back .brand__mark { width: 60px; height: 60px; }

  .name-band {
    position: absolute;
    left: 0; top: 260px;
    width: 720px; height: 56px;
    background: var(--navy);
    color: #fff;
    padding-left: 95px;
    display: flex; align-items: center;
    font-size: 28px;
  }
  .name-band__title { font-size: 20px; margin-left: 6px; margin-top: 5px; }
  .name-band__accent {
    position: absolute;
    left: 732px; top: 260px;
    width: 108px; height: 56px;
    background: var(--grey);
  }

  .contact {
    position: absolute;
    left: 95px; top: 343px;
    list-style: none;
    font-size: 19px;
    line-height: 28px;
  }
  .contact__label { font-weight: 700; font-style: italic; }
  .address {
    position: absolute;
    left: 431px; top: 399px;
    font-size: 19px;
    line-height: 28px;
    font-style: normal;
  }
</style>
</head>
<body>
  <section class="card card--front">
    <div class="brand"><span class="brand__mark"></span><span class="brand__name">KRL</span></div>

    <div class="name-band">Your Name,<span class="name-band__title">Designation</span></div>
    <div class="name-band__accent"></div>

    <ul class="contact">
      <li><span class="contact__label">t</span> : 123-123-1234</li>
      <li><span class="contact__label">f</span> : 123-123-1234</li>
      <li><span class="contact__label">e</span> : info@krl-example.com.sa</li>
      <li><span class="contact__label">w</span> : www.krl-example.com.sa</li>
    </ul>
    <address class="address">1234, Suite# 123, Street Name<br>State Name, Country Code</address>
  </section>

  <section class="card card--back">
    <div class="brand"><span class="brand__mark"></span><span class="brand__name">KRL</span></div>
  </section>
</body>
</html>
```